Business cards in digital learning for freelancer

Hello, I need a business cards in french. I work in the Digital learning industries as freeelancer; I'm an expert in digital learning. I work in France. My customer are in the health industry, pharmaceutical industry, and training organization. I've got a logo. I offer three services: consulting, Design, and Training. In the consulting, I offers coaching to choose your digital learning tools and the digital learning strategy. For the Design, I product differents level of elearning like rapid-learning, elearning, micro-learning, video-learning. And for the training service, I've create training about pedagogy, digital learning management project, Digital learning design.
I join my Logo create in this platform. My universe is gamified. I like the life, and I'm very social. I want a card like I'm I. I love Art (painting), Europeen comics. I use in my visual support "permanent maker" font and caracters. I would like cards: elegant, modern, Top class. If you need any information, you can ask me.
thanks for ideas

Target Market(s)

in health industries and training organization for Training manager, instructor, human resources director

Contact Information for Business Card

Phone number : 06 71 38 95 14 , mail: bastiengolmier@quelmoto.fr, web: bastiengolmier.fr , Carrivo

Font styles to use
Sans Serif

Requirements
Must have
• Use my logo and write my 3 services (consulting, training, design)

```html
<!DOCTYPE html>
<html lang="fr">
<head>
<meta charset="utf-8">
<title>Quelmoto — cartes de visite</title>
<link rel="stylesheet" href="https://fonts.googleapis.com/css2?family=Arimo:wght@400;700&family=Cinzel:wght@500&display=swap">
<style>
  :root {
    --page: #1c1c1c;
    --card: #0d0d0d;
    --card-edge: #161616;
    --orange: #f26b1d;
    --silver: #c9c9c9;
    --muted: #8a8a8a;
    --rule: #3a3a3a;
  }
  * { box-sizing: border-box; margin: 0; padding: 0; }
  html, body {
    width: 1200px; height: 900px; overflow: hidden;
    background: var(--page);
  }
  body {
    display: flex; flex-direction: column; align-items: center; justify-content: center;
    gap: 50px;
    font-family: "Arimo", Arial, sans-serif;
  }
  .card {
    position: relative;
    width: 560px; height: 320px;
    background: radial-gradient(circle at 40% 35%, var(--card-edge), var(--card) 70%);
    border-radius: 22px;
    overflow: hidden;
  }

  /* Front */
  .card-front .brand {
    position: absolute; left: 0; top: 0; width: 300px; height: 100%;
    display: flex; align-items: center; justify-content: center; gap: 12px;
  }
  .brand-dot {
    width: 18px; height: 18px; border-radius: 50%; background: var(--orange);
  }
  .brand-name {
    font-family: "Arimo", Arial, sans-serif; font-weight: 700;
    font-size: 40px; letter-spacing: 1px; color: var(--orange);
  }
  .card-front .divider {
    position: absolute; left: 300px; top: 60px; width: 1px; height: 200px;
    background: linear-gradient(var(--card), var(--rule) 30%, var(--rule) 70%, var(--card));
  }
  .contact {
    position: absolute; left: 330px; top: 78px; width: 220px;
  }
  .person-name {
    font-family: "Cinzel", "Times New Roman", serif; font-weight: 500;
    font-size: 22px; color: var(--orange); line-height: 1.1;
  }
  .person-role {
    font-size: 15px; color: var(--silver); margin-bottom: 22px;
  }
  .contact-list { list-style: none; }
  .contact-list li {
    display: flex; align-items: center; gap: 7px;
    font-size: 13.5px; color: var(--silver); line-height: 1.55;
    white-space: nowrap;
  }
  .contact-list svg { width: 13px; height: 13px; flex: none; }

  /* Back */
  .card-back .brand {
    position: absolute; left: 0; right: 0; top: 70px;
    display: flex; align-items: center; justify-content: center; gap: 12px;
  }
  .card-back .brand-dot { background: var(--silver); }
  .card-back .brand-name { color: var(--silver); }
  .social {
    position: absolute; left: 0; right: 0; top: 168px;
    display: flex; align-items: center; justify-content: center; gap: 14px;
  }
  .social .rule { width: 130px; height: 1px; background: var(--rule); }
  .social-badge {
    display: flex; align-items: center; gap: 6px;
    font-size: 13px; color: #ffffff;
  }
  .social-badge .circle {
    width: 14px; height: 14px; border-radius: 50%; background: #ffffff;
  }
  .services {
    position: absolute; left: 0; right: 0; top: 212px;
    display: flex; align-items: center; justify-content: center; gap: 10px;
    font-size: 15px; letter-spacing: 0.5px; color: var(--silver);
  }
  .services .sep {
    width: 8px; height: 8px; border-radius: 50%; background: #ffffff;
  }
</style>
</head>
<body>

  <section class="card card-front">
    <div class="brand">
      <span class="brand-dot"></span>
      <span class="brand-name">QUELMOTO</span>
    </div>
    <div class="divider"></div>
    <div class="contact">
      <p class="person-name">Bastien Golmier</p>
      <p class="person-role">Managing Director</p>
      <ul class="contact-list">
        <li>
          <svg viewBox="0 0 16 16" aria-hidden="true"><path fill="var(--orange)" d="M3.6 1.5l2.3 2.6-1.2 1.7c.9 2 2.5 3.6 4.5 4.5l1.7-1.2 2.6 2.3-1.4 2.2C6.8 13.3 2.7 9.2 1.4 3l2.2-1.5z"/></svg>
          06 71 38 95 14
        </li>
        <li>
          <svg viewBox="0 0 16 16" aria-hidden="true"><rect x="1" y="3" width="14" height="10" fill="var(--orange)"/><path d="M1 3l7 6 7-6" fill="none" stroke="var(--card)" stroke-width="1.3"/></svg>
          bastiengolmier@quelmoto.fr
        </li>
        <li>
          <svg viewBox="0 0 16 16" aria-hidden="true"><g fill="none" stroke="var(--orange)" stroke-width="1.4"><circle cx="8" cy="8" r="6.3"/><ellipse cx="8" cy="8" rx="2.7" ry="6.3"/><path d="M1.7 8h12.6M2.8 4.8h10.4M2.8 11.2h10.4"/></g></svg>
          www.bastiengolmier.fr
        </li>
      </ul>
    </div>
  </section>

  <section class="card card-back">
    <div class="brand">
      <span class="brand-dot"></span>
      <span class="brand-name">QUELMOTO</span>
    </div>
    <div class="social">
      <span class="rule"></span>
      <span class="social-badge"><span class="circle"></span>Carrivo</span>
      <span class="rule"></span>
    </div>
    <p class="services">
      <span>CONSULTING</span><span class="sep"></span>
      <span>TRAINING</span><span class="sep"></span>
      <span>DESIGN</span>
    </p>
  </section>

</body>
</html>
```